RW Framewell Inc Business cards

We need business cards using our existing logo but slightly modified. Right now the logo says RW Loadbearing Masonry. We want to keep the RW part of the design, but replace the Structural Concrete portion with "FRAMEWELL". Please see the attached file.
Ideally this would be a blank template so we can add Different Names, titles, and phone numbers later.
On the one side we want only the logo and on the other side the detail. I'm attaching an example for you to see.
Please reach out with any other questions. Our address and other details will be given out once we find a design we like.

Target Market(s)

Construction Industry

```html
<!DOCTYPE html>
<html lang="en">
<head>
<meta charset="utf-8">
<title>RW Framewell Inc – Business Card</title>
<link href="https://fonts.googleapis.com/css2?family=Archivo:wght@800&family=Roboto:wght@400&display=swap" rel="stylesheet">
<style>
  :root {
    --page: #eceef0;
    --brand-blue: #1c76bd;
    --brand-grey: #808285;
    --white: #ffffff;
    --disc-top: rgba(255, 255, 255, 0.92);
    --disc-bottom: rgba(240, 232, 234, 0.92);
  }
  * { margin: 0; padding: 0; box-sizing: border-box; }
  html, body {
    width: 1200px;
    height: 900px;
    overflow: hidden;
    background: var(--page);
  }
  .business-card {
    position: absolute;
    left: 100px;
    top: 141px;
    width: 1000px;
    height: 618px;
    background: var(--brand-grey);
    overflow: hidden;
    box-shadow: 0 10px 30px rgba(0, 0, 0, 0.15);
  }
  .blue-panel {
    position: absolute;
    left: 0;
    top: 0;
    width: 679px;
    height: 100%;
    background: var(--brand-blue);
  }
  .logo-disc {
    position: absolute;
    left: 413px;
    top: 43px;
    width: 532px;
    height: 532px;
    border-radius: 50%;
    background: radial-gradient(circle at 50% 40%, var(--disc-top), var(--disc-bottom));
  }
  .wordmark {
    position: absolute;
    left: 413px;
    top: 43px;
    width: 532px;
    height: 532px;
    display: flex;
    flex-direction: column;
    align-items: center;
    justify-content: center;
    font-family: "Archivo", "Arial Black", sans-serif;
    font-weight: 800;
    color: var(--brand-blue);
    text-align: center;
  }
  .wordmark-initials {
    font-size: 172px;
    line-height: 150px;
    letter-spacing: 4px;
  }
  .wordmark-name {
    font-size: 42px;
    line-height: 48px;
    letter-spacing: 3px;
    margin-top: 8px;
  }
  .contact-block {
    position: absolute;
    left: 49px;
    top: 186px;
    color: var(--white);
    font-family: "Roboto", Arial, sans-serif;
  }
  .person-name {
    font-family: "Archivo", "Arial Black", sans-serif;
    font-weight: 800;
    font-size: 34px;
    line-height: 38px;
    letter-spacing: 0.5px;
  }
  .person-title {
    font-size: 29px;
    line-height: 34px;
  }
  .contact-list {
    list-style: none;
    margin-top: 62px;
  }
  .contact-item {
    display: flex;
    align-items: center;
    font-size: 28px;
    line-height: 39px;
  }
  .contact-icon {
    width: 31px;
    height: 28px;
    margin-right: 8px;
    flex: none;
  }
</style>
</head>
<body>
  <div class="business-card">
    <div class="blue-panel"></div>
    <div class="logo-disc"></div>
    <div class="wordmark">
      <span class="wordmark-initials">RW</span>
      <span class="wordmark-name">FRAMEWELL</span>
    </div>

    <div class="contact-block">
      <h1 class="person-name">DANIEL REEVES</h1>
      <p class="person-title">Managing Director</p>
      <ul class="contact-list">
        <li class="contact-item">
          <svg class="contact-icon" viewBox="0 0 24 24" aria-hidden="true">
            <path fill="none" stroke="#fff" stroke-width="2" stroke-linejoin="round" d="M5 3h4l2 5-2.5 1.5a11 11 0 0 0 6 6L16 13l5 2v4a2 2 0 0 1-2 2A17 17 0 0 1 3 5a2 2 0 0 1 2-2z"/>
            <path fill="none" stroke="#fff" stroke-width="1.6" d="M14 3a7 7 0 0 1 7 7M14 6.5a3.5 3.5 0 0 1 3.5 3.5"/>
          </svg>
          044-987 654 321
        </li>
        <li class="contact-item">
          <svg class="contact-icon" viewBox="0 0 24 24" aria-hidden="true">
            <rect x="1" y="5" width="22" height="14" fill="#fff"/>
            <path fill="none" stroke="#1c76bd" stroke-width="1.6" d="M1 5l11 8 11-8M1 19l8-7M23 19l-8-7"/>
          </svg>
          hello@framewellmail.com
        </li>
        <li class="contact-item">
          <svg class="contact-icon" viewBox="0 0 24 24" aria-hidden="true">
            <g fill="none" stroke="#fff" stroke-width="1.6">
              <circle cx="12" cy="12" r="10"/>
              <ellipse cx="12" cy="12" rx="4.5" ry="10"/>
              <path d="M2 12h20M3.5 7h17M3.5 17h17M12 2v20"/>
            </g>
          </svg>
          www.framewellsite.com
        </li>
      </ul>
    </div>
  </div>
</body>
</html>
```